Infographic for a Christian church discipleship pathway

We need to take a fairly complex program that helps people in a Baptist church follow Jesus, and turn it into a simple graphic. This graphic does not have to explain the whole program, web pages and print materials will do that. But, it should be something that people see and understand what it is quickly. The attached graphic is only to give the key words and general direction of the program. It should not serve as a design guide. In other words, we want to see some other ideas how this information can be imparted graphically with concision and creativity. It's important to note, the categories at the top (pray daily, read daily, gather weekly) are first steps, starting points....one shouldn't move forward until they've incorporated these things into their life. However, the categories that follow (study, connect, serve, etc) are not necessarily steps to take in sequential order.

The diagrams we've provided are not what we expect. They are only to explain the program. Here is a verbal description: The motto of our church is "A Ready Church" (ready to serve, ready to love, ready for when Jesus returns). There are four words that describe a ready church member: FOCUSED on the return of Christ, FAITHFUL in a daily relationship with Jesus, PREPARED for any opportunity to be a supernatural vessel of God's worK, LOOKING to invite others into God's family. The first two are God's Work in Me (Focused and faithful); the second two are God's Work Through me (Prepared, looking). Please use those two things as you wish (Focused faithful prepared looking; and God's word in and through me). If they are clarifying, please use. If not, you don't have to use.

Additionally, the strategies we employ to be "a ready church" are 1. Prayer 2. God's Word, and 3. Biblical Community. (So, in other words, these three things help us be a people who is focused, faithful, prepared, and looking....which is a ready church.

To provide some information how we will build this out: this graphic will be used in print and digital content. The digital content will allow people to click on each category to access training and resources associated with that discipline. (Fasting, reflecting, etc).

www.kvt.church

Target Market(s)

35-50

Industry/Entity Type

Religious

Other font styles liked:
• Lato and/or Cambria

Requirements
Must have
• Fonts: lato, cambria. Colors#: 373E41, ebebe8, #a69677. Accent Colors: 80401D, #4e5730, #a5bac8
Nice to have
• A designer who has an understanding of what it means to incorporate the spiritual disciplines of the Christian faith into their life.

```html
<!DOCTYPE html>
<html lang="en">
<head>
<meta charset="utf-8">
<title>The Steady Path</title>
<link rel="stylesheet" href="https://fonts.googleapis.com/css2?family=Lato:wght@400;700;900&display=swap">
<style>
  :root {
    --ink: #373E41;
    --paper: #ebebe8;
    --gold: #a69677;
    --rust: #80401D;
    --rust-light: #97552f;
    --olive: #4e5730;
    --sky: #a5bac8;
    --sky-dark: #9db2c1;
    --sky-light: #b6c7d2;
    --taupe: #857960;
    --taupe-light: #9a8e74;
    --white: #ffffff;
  }
  * { margin: 0; padding: 0; box-sizing: border-box; }
  html, body { width: 1200px; height: 1063px; overflow: hidden; background: var(--white); }
  .canvas {
    position: relative;
    width: 1200px;
    height: 1063px;
    overflow: hidden;
    font-family: "Lato", Arial, sans-serif;
    color: var(--ink);
    background:
      linear-gradient(to bottom, rgba(255,255,255,0) 70%, #ffffff 96%),
      radial-gradient(ellipse 90% 80% at 60% 20%, #fafaf9 0%, #e6e6e3 60%, #dcdcd9 100%);
  }
  .cloud-band {
    position: absolute;
    left: 0; right: 0; bottom: 0;
    height: 170px;
    background: linear-gradient(to bottom, rgba(255,255,255,0), rgba(255,255,255,0.95) 55%, #fff);
  }
  .masthead { position: absolute; left: 112px; top: 100px; }
  .masthead__title {
    font-weight: 900;
    font-size: 58px;
    letter-spacing: 0.5px;
    line-height: 1;
    color: var(--ink);
  }
  .masthead__tagline {
    margin-top: 34px;
    font-weight: 700;
    font-size: 17px;
    letter-spacing: 2px;
    color: var(--gold);
  }
  .church-name {
    position: absolute;
    left: 862px;
    top: 98px;
    display: flex;
    align-items: center;
    gap: 14px;
  }
  .church-name__mark { width: 40px; height: 40px; background: var(--ink); }
  .church-name__text {
    font-weight: 700;
    font-size: 19px;
    line-height: 1.15;
    letter-spacing: 0.5px;
    color: var(--ink);
  }
  .diagram { position: absolute; left: 0; top: 0; width: 1200px; height: 1063px; }
  .phase-title { font-weight: 700; font-size: 13.5px; fill: var(--ink); }
  .phase-sub { font-weight: 400; font-size: 10.5px; fill: var(--ink); }
  .label { font-weight: 700; font-size: 11px; fill: var(--white); letter-spacing: 0.3px; }
  .step-daily { font-weight: 400; font-size: 11px; fill: var(--white); }
  .step { font-weight: 400; font-size: 11px; fill: var(--ink); }
  .badge circle { fill: var(--ink); stroke: var(--white); stroke-width: 1.4; }
  .badge text { font-weight: 900; font-size: 9px; fill: var(--white); }
  .outline { fill: rgba(255,255,255,0.35); stroke-width: 1.1; }
  .outline--prayer { stroke: #b4bfc6; }
  .outline--word { stroke: var(--taupe); }
  .outline--community { stroke: var(--rust); }
</style>
</head>
<body>
<div class="canvas">
  <div class="cloud-band"></div>

  <header class="masthead">
    <h1 class="masthead__title">THE STEADY PATH</h1>
    <p class="masthead__tagline">HABITS &amp; DISCIPLINES FOR A WHOLE LIFE</p>
  </header>

  <div class="church-name">
    <span class="church-name__mark"></span>
    <span class="church-name__text">KENT<br>VALLEY<br>TABERNACLE</span>
  </div>

  <svg class="diagram" viewBox="0 0 640 569" preserveAspectRatio="none" xmlns="http://www.w3.org/2000/svg">
    <defs>
      <linearGradient id="steepleTone" x1="0" y1="0" x2="0" y2="1">
        <stop offset="0" stop-color="#373E41"/>
        <stop offset="0.3" stop-color="#373E41"/>
        <stop offset="0.36" stop-color="#f6f6f4"/>
        <stop offset="1" stop-color="#f0f0ee"/>
      </linearGradient>
    </defs>

    <rect class="steeple" x="72" y="135" width="58" height="390" rx="4" fill="url(#steepleTone)" role="img" aria-label="Illustration of a white church steeple with dark spire"/>

    <g class="phase-heading" text-anchor="middle">
      <text class="phase-title" x="351" y="193">Focused. Faithful.</text>
      <text class="phase-sub" x="351" y="213">God’s Work In Me</text>
      <text class="phase-title" x="512" y="193">Prepared. Looking.</text>
      <text class="phase-sub" x="512" y="213">God’s Work Through Me</text>
    </g>

    <g class="path-row path-row--prayer">
      <polygon points="40,240 150,240 162,261 150,282 40,282 52,261" fill="var(--sky-dark)"/>
      <polygon points="152,240 264,240 276,261 264,282 152,282 164,261" fill="var(--sky-light)"/>
      <polygon class="outline outline--prayer" points="266,240 425,240 437,261 425,282 266,282 278,261"/>
      <polygon class="outline outline--prayer" points="428,240 585,240 597,261 585,282 428,282 440,261"/>
      <g text-anchor="middle">
        <text class="label" x="102" y="265">PRAYER</text>
        <text class="step-daily" x="214" y="265">Prayer Daily</text>
        <text class="step" x="320" y="265">Rest</text>
        <text class="step" x="384" y="265">Reflect</text>
        <text class="step" x="481" y="265">Fast</text>
        <text class="step" x="543" y="265">Intercede</text>
      </g>
    </g>

    <g class="path-row path-row--word">
      <polygon points="40,327 150,327 162,348 150,369 40,369 52,348" fill="var(--taupe)"/>
      <polygon points="152,327 264,327 276,348 264,369 152,369 164,348" fill="var(--taupe-light)"/>
      <polygon class="outline outline--word" points="266,327 425,327 437,348 425,369 266,369 278,348"/>
      <polygon class="outline outline--word" points="428,327 585,327 597,348 585,369 428,369 440,348"/>
      <g text-anchor="middle">
        <text class="label" x="102" y="352">WORD</text>
        <text class="step-daily" x="214" y="352">Word Daily</text>
        <text class="step" x="320" y="352">Study</text>
        <text class="step" x="384" y="352">Memorize</text>
        <text class="step" x="488" y="352">Teach</text>
        <text class="step" x="543" y="352">Proclaim</text>
      </g>
    </g>

    <g class="path-row path-row--community">
      <polygon points="40,414 150,414 162,435 150,456 40,456 52,435" fill="var(--rust)"/>
      <polygon points="152,414 264,414 276,435 264,456 152,456 164,435" fill="var(--rust-light)"/>
      <polygon class="outline outline--community" points="266,414 425,414 437,435 425,456 266,456 278,435"/>
      <polygon class="outline outline--community" points="428,414 585,414 597,435 585,456 428,456 440,435"/>
      <g text-anchor="middle">
        <text class="label" x="102" y="439">COMMUNITY</text>
        <text class="step-daily" x="214" y="439">Community Daily</text>
        <text class="step" x="319" y="439">Connect</text>
        <text class="step" x="384" y="439">Learn</text>
        <text class="step" x="481" y="439">Give</text>
        <text class="step" x="543" y="439">Serve</text>
      </g>
    </g>

    <g class="badges" text-anchor="middle">
      <g class="badge"><circle cx="57" cy="240" r="7.5"/><text x="57" y="243.3">P</text></g>
      <g class="badge"><circle cx="214" cy="239" r="7.5"/><text x="214" y="242.3">1</text></g>
      <g class="badge"><circle cx="351" cy="239" r="7.5"/><text x="351" y="242.3">2</text></g>
      <g class="badge"><circle cx="512" cy="239" r="7.5"/><text x="512" y="242.3">3</text></g>

      <g class="badge"><circle cx="57" cy="327" r="7.5"/><text x="57" y="330.3">W</text></g>
      <g class="badge"><circle cx="214" cy="326" r="7.5"/><text x="214" y="329.3">1</text></g>
      <g class="badge"><circle cx="351" cy="326" r="7.5"/><text x="351" y="329.3">2</text></g>
      <g class="badge"><circle cx="512" cy="326" r="7.5"/><text x="512" y="329.3">3</text></g>

      <g class="badge"><circle cx="57" cy="414" r="7.5"/><text x="57" y="417.3">C</text></g>
      <g class="badge"><circle cx="214" cy="413" r="7.5"/><text x="214" y="416.3">1</text></g>
      <g class="badge"><circle cx="351" cy="413" r="7.5"/><text x="351" y="416.3">2</text></g>
      <g class="badge"><circle cx="512" cy="413" r="7.5"/><text x="512" y="416.3">3</text></g>
    </g>
  </svg>
</div>
</body>
</html>
```